K7 Services business card design contest. Use logo and create a professional layout.

See attached sample. Please sharpen all text and images, don't want any pix-elated content. We are looking for a clean look that quickly provides the information need. Please include our information provided on the sample card. Please feel free to offer any design changes. Please only user the colors provided: #2D3539 & #FFA500. Do not prefer any images other than the K7 Logo

Target Market(s)

Construction, Architects, General Contractors, residential

Industry/Entity Type

Business

Contact Information for Business Card

Company logo, Name, email, fax & phone

Font styles to use
Other font styles liked:
• Josefin Slab

Requirements
Must have
• Name
• Phone & Fax #'s
• address
• Logo
• Website url: www.kq7services.example
Nice to have
• Font Colors #2D3539 & #FFA400
• We prefer a white background.

```html
<!DOCTYPE html>
<html lang="en">
<head>
<meta charset="utf-8">
<title>K7 Services – Business Card</title>
<link rel="stylesheet" href="https://fonts.googleapis.com/css2?family=Montserrat:wght@400;500;600&display=swap">
<style>
  :root {
    --ink: #2D3539;
    --accent: #F0962A;
    --paper: #FFFFFF;
    --backdrop: #E6E6E6;
    --muted: #4a5357;
  }
  * { box-sizing: border-box; margin: 0; padding: 0; }
  html, body {
    width: 1200px; height: 852px; overflow: hidden;
    background: var(--backdrop);
    font-family: "Montserrat", Arial, sans-serif;
    color: var(--ink);
  }
  .stage { position: relative; width: 1200px; height: 852px; }
  .card {
    position: absolute;
    width: 560px; height: 320px;
    background: var(--paper);
    border-radius: 14px;
    box-shadow: 0 6px 18px rgba(0,0,0,0.18);
    overflow: hidden;
  }
  .card--front { left: 130px; top: 90px; }
  .card--back  { left: 510px; top: 440px; }

  .brand-name {
    font-weight: 600;
    color: var(--ink);
    letter-spacing: 0.5px;
    display: flex; align-items: center; gap: 12px;
  }
  .brand-name .brand-dot {
    width: 14px; height: 14px; border-radius: 50%;
    background: var(--ink);
  }
  .card--front .brand-name {
    position: absolute; left: 0; right: 0; top: 50%;
    transform: translateY(-50%);
    justify-content: center;
    font-size: 46px;
  }

  .side-band {
    position: absolute; left: 0; top: 0; bottom: 0; width: 58px;
    background: var(--accent);
  }
  .side-rule {
    position: absolute; left: 58px; top: 0; bottom: 0; width: 7px;
    background: var(--ink);
  }
  .back-content { position: absolute; left: 100px; top: 34px; right: 30px; bottom: 28px; }
  .card--back .brand-name { font-size: 30px; }
  .person-name { margin-top: 26px; font-size: 17px; color: var(--accent); font-weight: 400; }
  .person-role { margin-top: 4px; font-size: 12.5px; color: var(--ink); }
  .address { margin-top: 16px; font-size: 11.5px; line-height: 1.5; color: var(--muted); }
  .contact-list { margin-top: 8px; list-style: none; font-size: 11.5px; color: var(--muted); }
  .contact-list li { display: flex; align-items: center; gap: 10px; line-height: 1.75; }
  .contact-list svg { width: 13px; height: 13px; fill: var(--accent); flex: none; }
  .services {
    position: absolute; right: 30px; bottom: 84px;
    font-size: 12.5px; letter-spacing: 0.6px; color: var(--ink);
  }
</style>
</head>
<body>
<main class="stage">
  <section class="card card--front" aria-label="Card front">
    <div class="brand-name"><span class="brand-dot"></span>K7 Services</div>
  </section>

  <section class="card card--back" aria-label="Card back">
    <div class="side-band"></div>
    <div class="side-rule"></div>
    <div class="back-content">
      <div class="brand-name"><span class="brand-dot"></span>K7 Services</div>
      <p class="person-name">Daniel R. Holloway, MBA</p>
      <p class="person-role">Director of Operations</p>
      <p class="address">2170 Maplecrest Road, Suite<br>410-118 Fairview, Georgia, 30099</p>
      <ul class="contact-list">
        <li>
          <svg viewBox="0 0 16 16" aria-hidden="true"><path d="M3.5 1.5l2.5 0 1 3.5-1.8 1.2a8 8 0 0 0 4.6 4.6l1.2-1.8 3.5 1v2.5c0 .8-.7 1.5-1.5 1.5A12 12 0 0 1 2 3c0-.8.7-1.5 1.5-1.5z"/></svg>
          (555) 318 - 4426
        </li>
        <li>
          <svg viewBox="0 0 16 16" aria-hidden="true"><path d="M4 1h7v4H4zM2 6h12v7H2zM4 13h8v2H4z"/></svg>
          (555) 672 - 1950
        </li>
        <li>
          <svg viewBox="0 0 16 16" aria-hidden="true"><circle cx="8" cy="8" r="6.5" fill="none" stroke="#F0962A" stroke-width="1.5"/><path d="M1.5 8h13M8 1.5c-3 3.5-3 9.5 0 13M8 1.5c3 3.5 3 9.5 0 13" fill="none" stroke="#F0962A" stroke-width="1.2"/></svg>
          www.kq7services.example
        </li>
      </ul>
      <p class="services">DRONE | WEBCAM | VIDEO</p>
    </div>
  </section>
</main>
</body>
</html>
```